Meridale Bed Company Needs Business Card

Looking for a very nice looking business card. Creative but not extravagant. We sell beds and pillows across the U.S. and need something professional but catchy. I have attached the logo.

Name : Devin Holt
Title : President
Phone : (800) 471-2960
Email: sleep@quilmora.com
Website: www.quilmora.com

Can be single-sided or double-sided
horizontal or vertical

Can use Blues/Greys

Target Market(s)

Mass Market

Industry/Entity Type

Retail

Contact Information for Business Card

Name : Devin Holt
Title : President
Phone : (800) 471-2960
Email: sleep@quilmora.com
Website: www.quilmora.com

Requirements
Must have
• Clean, Modern, Smooth
• Can use Blues/Greys
• On the other side without the information - have something simple like www.quilmora.com or our logo
Nice to have
• Surprise me
Should not have
• Nothing crazy, nothing cluttered

```html
<!DOCTYPE html>
<html lang="en">
<head>
<meta charset="UTF-8">
<title>Quilmora Business Card</title>
<link rel="stylesheet" href="https://fonts.googleapis.com/css2?family=Montserrat:wght@300;400;600&display=swap">
<style>
  :root {
    --stage: #2b2b2d;
    --card: #050505;
    --brand-blue: #2ea3dc;
    --text-light: #f2f2f2;
    --divider: #8a8a8a;
  }
  * { margin: 0; padding: 0; box-sizing: border-box; }
  html, body {
    width: 1200px;
    height: 900px;
    overflow: hidden;
    background: var(--stage);
    font-family: "Montserrat", sans-serif;
  }
  .stage {
    position: relative;
    width: 1200px;
    height: 900px;
  }
  .card {
    position: absolute;
    left: 337px;
    width: 526px;
    height: 300px;
    background: var(--card);
    border-radius: 18px;
    overflow: hidden;
    box-shadow: 0 12px 30px rgba(0,0,0,0.55);
  }
  .card--front { top: 110px; }
  .card--back { top: 490px; }

  .wordmark {
    font-family: "Montserrat", sans-serif;
    font-weight: 300;
    color: var(--brand-blue);
    letter-spacing: 1px;
    line-height: 1;
    white-space: nowrap;
  }
  .card--front .wordmark {
    position: absolute;
    top: 92px;
    left: 0;
    right: 0;
    text-align: center;
    font-size: 82px;
  }
  .front-url {
    position: absolute;
    bottom: 34px;
    left: 0;
    right: 0;
    text-align: center;
    font-size: 16px;
    font-weight: 400;
    color: var(--text-light);
    letter-spacing: 0.3px;
  }
  .front-url .accent,
  .contact-list .accent { color: var(--brand-blue); }

  .card--back .wordmark {
    position: absolute;
    top: 132px;
    left: 36px;
    font-size: 50px;
  }
  .divider {
    position: absolute;
    left: 294px;
    top: 82px;
    width: 1px;
    height: 118px;
    background: linear-gradient(to bottom, rgba(138,138,138,0), var(--divider) 30%, var(--divider) 70%, rgba(138,138,138,0));
  }
  .contact {
    position: absolute;
    left: 312px;
    top: 82px;
    color: var(--text-light);
  }
  .contact-name {
    font-size: 20px;
    font-weight: 600;
    color: var(--brand-blue);
    line-height: 1.1;
  }
  .contact-title {
    font-size: 13px;
    font-weight: 400;
    margin-bottom: 14px;
  }
  .contact-list { list-style: none; }
  .contact-list li {
    display: flex;
    align-items: center;
    gap: 8px;
    font-size: 13px;
    line-height: 1.55;
    white-space: nowrap;
  }
  .contact-list svg {
    width: 10px;
    height: 10px;
    flex: none;
  }
  .edge-band {
    position: absolute;
    top: 0;
    right: 0;
    width: 9px;
    height: 142px;
    background: var(--brand-blue);
    border-bottom-left-radius: 6px;
  }
</style>
</head>
<body>
<main class="stage">
  <section class="card card--front">
    <div class="wordmark">quilmora</div>
    <p class="front-url">www.<span class="accent">quilmora</span>.com</p>
  </section>

  <section class="card card--back">
    <span class="edge-band"></span>
    <div class="wordmark">quilmora</div>
    <span class="divider"></span>
    <div class="contact">
      <h1 class="contact-name">Devin Holt</h1>
      <p class="contact-title">President</p>
      <ul class="contact-list">
        <li>
          <svg viewBox="0 0 10 10" aria-hidden="true"><path d="M2.2 0.8 L3.6 2.8 L2.8 3.8 Q3.8 5.8 6.2 7.2 L7.2 6.4 L9.2 7.8 L8.4 9.2 Q4.8 9.4 2.2 6.8 Q0.4 4.6 0.8 1.6 Z" fill="var(--brand-blue)"/></svg>
          <span class="contact-text">(800) 471-2960</span>
        </li>
        <li>
          <svg viewBox="0 0 10 10" aria-hidden="true"><rect x="0.8" y="2" width="8.4" height="6" fill="none" stroke="var(--brand-blue)" stroke-width="1"/><path d="M0.8 2 L5 5.4 L9.2 2" fill="none" stroke="var(--brand-blue)" stroke-width="1"/></svg>
          <span class="contact-text">sleep@quilmora.com</span>
        </li>
        <li>
          <svg viewBox="0 0 10 10" aria-hidden="true"><circle cx="5" cy="5" r="4.2" fill="none" stroke="var(--brand-blue)" stroke-width="1"/><ellipse cx="5" cy="5" rx="1.8" ry="4.2" fill="none" stroke="var(--brand-blue)" stroke-width="0.8"/><line x1="0.8" y1="5" x2="9.2" y2="5" stroke="var(--brand-blue)" stroke-width="0.8"/></svg>
          <span class="contact-text">www.<span class="accent">quilmora</span>.com</span>
        </li>
      </ul>
    </div>
  </section>
</main>
</body>
</html>
```